Biz Card

MARKETING today is the most rapidly changing business discipline. Media options to reach customers, actual customer preferences and consumer buying decisions change by the minute . . . no, by the second. The behavioral data generated by all aspects of the business and the new technologies that put the data to work together produce the potential to generate business intelligence and guide smart resource allocation to influence purchase and retention. However, to realize this potential, marketing professionals at all levels and in all organizations must continuously improve their skills not just from on-the-job training but by learning from masters in the field. The Bright Horizon Guild is the training center that serves this professional development need.model logos:msi.orgama.orgcontentmarketinginstitute.comBook covers on MarketingMetrics, Marketing Anaytics
Industry/Entity Type
Business
Contact Information for Business Card
Roy A. YoungCEOMarketing Science Academyphone: 310-601-4755email: roy@marketingscience.comAddress:437 South Rexford DriveBeverly Hills, CA 89377
Look and feel
Each slider illustrates characteristics of the customer's brand and the style your logo design should communicate.

```html
<!DOCTYPE html>
<html lang="en">
<head>
<meta charset="utf-8">
<title>Bright Horizon Guild – Business Card</title>
<link rel="stylesheet" href="https://fonts.googleapis.com/css2?family=Roboto:wght@400;500;700&display=swap">
<style>
  :root {
    --backdrop: #e9e7e4;
    --card-dark: #1d1d1f;
    --card-dark-mark: #2c2c2e;
    --card-light: #ffffff;
    --brand-blue: #1257a3;
    --brand-green: #7ac231;
    --ink: #2b2b2b;
    --muted: #6d6d6d;
    --text-light: #f2f2f2;
  }
  * { box-sizing: border-box; margin: 0; padding: 0; }
  html, body { width: 1200px; height: 716px; overflow: hidden; }
  body {
    background: var(--backdrop);
    font-family: "Roboto", Arial, sans-serif;
    position: relative;
  }
  .card {
    position: absolute;
    top: 208px;
    width: 525px;
    height: 300px;
    border-radius: 4px;
    box-shadow: 0 10px 28px rgba(0,0,0,.22);
    overflow: hidden;
  }

  /* Back of card */
  .card-back { left: 50px; background: var(--card-dark); }
  .card-back .brand-block {
    position: absolute; left: 210px; top: 42px;
    width: 260px; height: 110px;
    border: 2px solid var(--card-dark-mark);
    display: flex; align-items: center; justify-content: center;
    color: #3b3b3e; font-weight: 700; font-size: 25px; text-align: center; line-height: 1.15;
  }
  .card-back .tagline-band {
    position: absolute; left: 0; right: 0; top: 168px; height: 28px;
    background: var(--brand-green);
    display: flex; align-items: center; padding-left: 34px;
    font-size: 14px; color: #1b3a06; font-weight: 500;
  }
  .card-back .website {
    position: absolute; left: 40px; top: 222px;
    color: var(--text-light); font-size: 15px;
  }

  /* Front of card */
  .card-front { left: 625px; background: var(--card-light); }
  .card-front .edge-blue {
    position: absolute; left: 0; top: 0; bottom: 0; width: 30px; background: var(--brand-blue);
  }
  .card-front .edge-green {
    position: absolute; left: 30px; top: 0; bottom: 0; width: 6px; background: var(--brand-green);
  }
  .brand-lockup {
    position: absolute; right: 30px; top: 50px;
    display: flex; align-items: center; gap: 10px;
  }
  .brand-lockup .dot { width: 14px; height: 14px; border-radius: 50%; background: var(--brand-green); }
  .brand-lockup .brand-name {
    font-size: 26px; font-weight: 700; color: var(--brand-blue); line-height: 1;
  }
  .person { position: absolute; left: 66px; top: 130px; }
  .person .name { font-size: 22px; font-weight: 700; color: var(--brand-blue); }
  .person .role { font-size: 12px; color: var(--muted); margin-top: 3px; }
  .contact-list { position: absolute; left: 66px; top: 196px; list-style: none; }
  .contact-list li {
    display: flex; align-items: center; gap: 10px;
    font-size: 14px; color: var(--ink); margin-bottom: 7px;
  }
  .contact-list svg { width: 13px; height: 13px; fill: var(--brand-blue); flex: none; }
</style>
</head>
<body>
  <section class="card card-back">
    <div class="brand-block">Bright Horizon<br>Guild</div>
    <div class="tagline-band">Executive Education in Marketing Analitics and Technology</div>
    <div class="website">www.brighthorizonguild.com</div>
  </section>

  <section class="card card-front">
    <div class="edge-blue"></div>
    <div class="edge-green"></div>
    <div class="brand-lockup">
      <span class="dot"></span>
      <span class="brand-name">Bright Horizon Guild</span>
    </div>
    <div class="person">
      <div class="name">Neil P. Barton</div>
      <div class="role">CEO</div>
    </div>
    <ul class="contact-list">
      <li>
        <svg viewBox="0 0 24 24" aria-hidden="true"><path d="M6.6 10.8a15 15 0 0 0 6.6 6.6l2.2-2.2a1 1 0 0 1 1-.25 11.4 11.4 0 0 0 3.6.57 1 1 0 0 1 1 1V20a1 1 0 0 1-1 1A17 17 0 0 1 3 4a1 1 0 0 1 1-1h3.5a1 1 0 0 1 1 1c0 1.25.2 2.45.57 3.6a1 1 0 0 1-.25 1z"/></svg>
        310-555-0182
      </li>
      <li>
        <svg viewBox="0 0 24 24" aria-hidden="true"><path d="M2 5h20v14H2zm2 2v.5l8 5 8-5V7l-8 5z"/></svg>
        neil@brighthorizonguild.com
      </li>
      <li>
        <svg viewBox="0 0 24 24" aria-hidden="true"><path d="M12 2a7 7 0 0 0-7 7c0 5 7 13 7 13s7-8 7-13a7 7 0 0 0-7-7zm0 9.5A2.5 2.5 0 1 1 12 6.5a2.5 2.5 0 0 1 0 5z"/></svg>
        912 North Calloway Lane Beverly Hills, CA 89377
      </li>
    </ul>
  </section>
</body>
</html>
```